Lumavento business card

We need a modern business card - With our 4 colors - See web: www.lumavento.dk

I have attached logo and som old business Cards we have - Lets Make the new ones shine...:-) -

Industry/Entity Type

Business

Requirements
Must have
• the logo with lumavento only,

```html
<!DOCTYPE html>
<html lang="da">
<head>
<meta charset="utf-8">
<title>Lumavento – visitkort</title>
<link rel="stylesheet" href="https://fonts.googleapis.com/css2?family=Source+Sans+3:wght@400;600&display=swap">
<style>
  :root {
    --lime: #8dc45e;
    --plum: #6a2a78;
    --magenta: #c9358a;
    --tangerine: #e3883f;
    --ink: #565656;
    --ink-dark: #3f3f3f;
    --rule: #5a5a5a;
    --paper: #ffffff;
    --backdrop: #e6e6e6;
  }
  * { box-sizing: border-box; margin: 0; padding: 0; }
  html, body {
    width: 1105px; height: 1200px; overflow: hidden;
    background: var(--backdrop);
    font-family: "Source Sans 3", "Myriad Pro", sans-serif;
  }
  .card {
    position: absolute; left: 102px;
    width: 900px; height: 514px;
    background: var(--paper);
    box-shadow: 0 4px 14px rgba(0,0,0,.18);
    overflow: hidden;
  }
  .card--front { top: 57px; }
  .card--back { top: 629px; }

  /* front: brand block */
  .brand {
    position: absolute; left: 574px; top: 148px; width: 281px;
    text-align: center;
  }
  .brand__name {
    display: block;
    font-size: 38px; font-weight: 600; letter-spacing: 1px;
    color: var(--ink-dark); line-height: 1;
  }
  .brand__rule {
    height: 3px; background: var(--lime); margin-top: 20px;
  }
  .brand__tagline {
    display: block; margin-top: 12px;
    font-size: 17px; color: var(--ink-dark);
  }

  /* front: person */
  .person { position: absolute; left: 45px; top: 275px; right: 45px; }
  .person__name {
    font-size: 34px; font-weight: 600; color: var(--lime); line-height: 1.1;
  }
  .person__role {
    display: flex; align-items: flex-end; gap: 6px;
    font-size: 22px; color: var(--ink-dark); line-height: 1.1;
  }
  .person__role::after {
    content: ""; flex: 1; height: 2px; background: var(--rule); margin-bottom: 4px;
  }

  /* front: contact */
  .contact {
    position: absolute; left: 50px; top: 360px; list-style: none;
    font-size: 24px; color: var(--ink);
  }
  .contact li { display: flex; align-items: center; height: 33px; }
  .contact svg { width: 20px; height: 20px; margin-right: 13px; fill: var(--lime); }

  .address {
    position: absolute; right: 45px; top: 366px; text-align: right;
    font-style: normal; font-size: 24px; line-height: 31px; color: var(--ink);
  }

  /* colour bands */
  .bands { position: absolute; display: flex; }
  .bands span { height: 100%; }
  .bands--strip { left: 0; right: 0; bottom: 0; height: 24px; gap: 5px; }
  .bands--full { inset: 0; }
  .band--lime { background: var(--lime); }
  .band--plum { background: var(--plum); }
  .band--magenta { background: var(--magenta); }
  .band--tangerine { background: var(--tangerine); }

  /* back: brand */
  .back-brand {
    position: absolute; left: 0; right: 0; top: 218px; text-align: center;
    font-size: 64px; font-weight: 600; letter-spacing: 2px;
    color: var(--paper); line-height: 1;
  }
</style>
</head>
<body>

<section class="card card--front">
  <div class="brand">
    <span class="brand__name">lumavento</span>
    <div class="brand__rule"></div>
    <span class="brand__tagline">medier til unge</span>
  </div>

  <div class="person">
    <p class="person__name">Maja Holmgaard</p>
    <p class="person__role">Salgsdirektør</p>
  </div>

  <ul class="contact">
    <li>
      <svg viewBox="0 0 24 24" aria-hidden="true"><path d="M6.6 10.8a15.1 15.1 0 0 0 6.6 6.6l2.2-2.2a1 1 0 0 1 1-.25 11.4 11.4 0 0 0 3.6.57 1 1 0 0 1 1 1V20a1 1 0 0 1-1 1A17 17 0 0 1 3 4a1 1 0 0 1 1-1h3.5a1 1 0 0 1 1 1c0 1.25.2 2.45.57 3.57a1 1 0 0 1-.25 1z"/></svg>
      +45 20 14 70 36
    </li>
    <li>
      <svg viewBox="0 0 24 24" aria-hidden="true"><path d="M6.6 10.8a15.1 15.1 0 0 0 6.6 6.6l2.2-2.2a1 1 0 0 1 1-.25 11.4 11.4 0 0 0 3.6.57 1 1 0 0 1 1 1V20a1 1 0 0 1-1 1A17 17 0 0 1 3 4a1 1 0 0 1 1-1h3.5a1 1 0 0 1 1 1c0 1.25.2 2.45.57 3.57a1 1 0 0 1-.25 1z"/></svg>
      +45 20 14 70 37
    </li>
    <li>
      <svg viewBox="0 0 24 24" aria-hidden="true"><path d="M2 5h20v14H2z M2 5l10 8 10-8" /><path d="M3 6l9 7 9-7" fill="#fff"/></svg>
      mh@lumavento.dk
    </li>
  </ul>

  <address class="address">
    Solsikkevej 14<br>
    2100 Nordhavn<br>
    www.lumavento.dk
  </address>

  <div class="bands bands--strip">
    <span class="band--lime" style="width:217px"></span>
    <span class="band--plum" style="width:217px"></span>
    <span class="band--magenta" style="width:223px"></span>
    <span class="band--tangerine" style="flex:1"></span>
  </div>
</section>

<section class="card card--back">
  <div class="bands bands--full">
    <span class="band--lime" style="width:219px"></span>
    <span class="band--plum" style="width:221px"></span>
    <span class="band--magenta" style="width:227px"></span>
    <span class="band--tangerine" style="flex:1"></span>
  </div>
  <p class="back-brand">lumavento</p>
</section>

</body>
</html>
```